Tree Service Billboard 20x8 ft

We need a billboard design for a tree service company.
The billboard is 20ft x 8 ft so we need a design that is capable to stretching to those dimensions without loosing quality.
I have attached a series of images.
Image 1- Simply a billboard that I think looks good that I would like you to use for inspiration. I am aiming for the same format only no color in the wording, just black white, or gray. I like the the trees in the background, the logo placed to the left, and wording on the right.
Image 2- Current Logo I would like to the left of the billboard
Image 3- Another format of current logo if needed.
Image 4- A drawn out design template
Image 5- Another drawn out design template

Specific things I am looking for
-The contact number to be the largest thing on the design
-The logo on the design
-Key points to the design to say:
Tree Removal
Tree Trimming
Land Development
Stump Grinding
Storm Response
Insured
Free Bids
-The facebook logo
-The Google Logo

```html
<!DOCTYPE html>
<html lang="en">
<head>
<meta charset="utf-8">
<title>Birchline Tree Service Billboard</title>
<link rel="stylesheet" href="https://fonts.googleapis.com/css2?family=Teko:wght@500;600&family=Noto+Serif:wght@700&display=swap">
<style>
  :root {
    --page-bg: #e8edf1;
    --forest-dark: #1f2a14;
    --forest-mid: #3b4d22;
    --forest-light: #6b7d3a;
    --tile-teal: #2a9870;
    --tile-green: #5da94a;
    --leaf-dark: #1f6b2c;
    --leaf-light: #4caf50;
    --band-white: #f7f7f5;
    --call-red: #e2212b;
    --white: #ffffff;
  }
  * { margin: 0; padding: 0; box-sizing: border-box; }
  html, body { width: 1200px; height: 675px; overflow: hidden; }
  body { background: var(--page-bg); position: relative; }

  .billboard {
    position: absolute; left: 40px; top: 113px;
    width: 1120px; height: 448px; overflow: hidden;
    background: var(--forest-dark);
  }
  .forest-photo {
    position: absolute; inset: 0;
    background:
      radial-gradient(ellipse at 30% 40%, var(--forest-light) 0%, transparent 45%),
      radial-gradient(ellipse at 75% 30%, var(--forest-mid) 0%, transparent 50%),
      linear-gradient(160deg, var(--forest-mid), var(--forest-dark));
  }
  .social-icons { position: absolute; left: 22px; top: 16px; display: flex; gap: 8px; list-style: none; }
  .social-icons li { width: 26px; height: 26px; border-radius: 50%; background: var(--white); display: block; }

  .corner-frame { position: absolute; left: 0; top: 0; }

  .brand { position: absolute; left: 50px; top: 36px; width: 480px; text-align: center; color: var(--white); }
  .brand-circle { width: 112px; height: 112px; border: 5px solid var(--white); border-radius: 50%; margin: 0 auto 14px; }
  .brand-name { font-family: 'Teko', sans-serif; font-weight: 600; font-size: 50px; line-height: 0.9; letter-spacing: 1px; white-space: nowrap; }
  .brand-phone { display: flex; align-items: center; gap: 12px; margin-top: 6px;
    font-family: 'Teko', sans-serif; font-weight: 500; font-size: 34px; line-height: 1; white-space: nowrap; }
  .brand-phone::before, .brand-phone::after { content: ""; flex: 1; height: 3px; background: var(--white); }

  .services {
    position: absolute; left: 560px; top: 62px; width: 500px;
    display: grid; grid-template-columns: 1fr 1fr; gap: 8px; list-style: none;
  }
  .service {
    height: 52px; display: flex; align-items: center; justify-content: center;
    font-family: 'Noto Serif', serif; font-weight: 700; color: var(--white);
    font-size: 19px; letter-spacing: 0.5px; text-transform: uppercase; white-space: nowrap;
  }
  .service--teal { background: var(--tile-teal); }
  .service--green { background: var(--tile-green); }
  .service--wide { grid-column: 1 / span 2; font-size: 26px; }
  .service--big { font-size: 24px; }

  .call-band {
    position: absolute; left: 0; right: 0; top: 330px; bottom: 0;
    background: var(--band-white);
  }
  .grass-edge { position: absolute; left: 0; top: 300px; width: 1120px; height: 40px; }
  .foliage {
    position: absolute; left: 0; top: 310px; width: 540px; height: 138px;
    background: linear-gradient(100deg, var(--leaf-dark), var(--leaf-light) 55%, rgba(76,175,80,0));
  }
  .foliage--right {
    left: auto; right: 0; width: 120px;
    background: linear-gradient(260deg, var(--leaf-dark), rgba(76,175,80,0));
  }
  .call-number {
    position: absolute; left: 590px; top: 342px;
    font-family: 'Teko', sans-serif; font-weight: 600; font-size: 92px; line-height: 1;
    color: var(--call-red); letter-spacing: 2px; white-space: nowrap;
  }
</style>
</head>
<body>
  <main class="billboard">
    <div class="forest-photo" role="img" aria-label="Aerial photo of a dense green forest canopy"></div>

    <svg class="corner-frame" width="240" height="200" viewBox="0 0 240 200" aria-hidden="true">
      <polyline points="100,0 190,72 20,170" fill="none" stroke="#ffffff" stroke-width="2"/>
    </svg>

    <ul class="social-icons" aria-label="Social profiles"><li></li><li></li></ul>

    <div class="brand">
      <div class="brand-circle"></div>
      <h1 class="brand-name">BIRCHLINE TREE SERVICE</h1>
      <p class="brand-phone">555-014-2290</p>
    </div>

    <ul class="services">
      <li class="service service--teal">Tree Removal</li>
      <li class="service service--teal">Tree Trimming</li>
      <li class="service service--green service--wide">Land Development</li>
      <li class="service service--teal">Stump Grinding</li>
      <li class="service service--teal">Storm Response</li>
      <li class="service service--green service--big">Insured</li>
      <li class="service service--green service--big">Free Bids</li>
    </ul>

    <svg class="grass-edge" viewBox="0 0 1120 40" preserveAspectRatio="none" aria-hidden="true">
      <path d="M0,10 Q120,0 240,14 T480,18 T720,24 T960,20 T1120,26 V40 H0 Z" fill="#3a8a3a"/>
      <path d="M0,18 Q140,10 280,22 T560,26 T840,30 T1120,32 V40 H0 Z" fill="#f7f7f5"/>
    </svg>
    <div class="call-band"></div>
    <div class="foliage" role="img" aria-label="Illustrated tropical leaves and ferns"></div>
    <div class="foliage foliage--right" role="img" aria-label="Illustrated tropical leaves"></div>
    <p class="call-number">555-014-2290</p>
  </main>
</body>
</html>
```